I need a business card design for my vidloomer channel called The Tidy Skillet Show. I make vidloomer cooking tutorials. I'd like the phrase " I'll see you next time, for my next meal" somewhere on the BC. The Vidloomer web address is www.vidloomer.example/user/TidySkilletShow
email - bookings@harrowlanemedia.example

Target Market(s)

This is for companies & business opportunities so it needs to look professional & sleek.

Industry/Entity Type

Cooking

Requirements
Must have
• Must have my Tidy skillet show logo on the card preferably top left. My name ( Marcus Delroy ). Name of my channel "Tidy Skillet Show" & the vidlomer logo & web address for my channel & the email bookings@harrowlanemedia.example & the 3 pics of food.

```html
<!DOCTYPE html>
<html lang="en">
<head>
<meta charset="utf-8">
<title>Tidy Skillet Show – Business Card</title>
<link href="https://fonts.googleapis.com/css2?family=Josefin+Sans:wght@600;700&family=Open+Sans:wght@400;600&display=swap" rel="stylesheet">
<style>
  :root {
    --ink-black: #0d0d0d;
    --brand-orange: #f59a1b;
    --paper-white: #ffffff;
    --stage-grey: #f2f2f2;
    --text-dark: #222222;
    --video-red: #d8262b;
    --mail-blue: #1f3c8f;
  }
  * { margin: 0; padding: 0; box-sizing: border-box; }
  html, body {
    width: 1200px; height: 1000px; overflow: hidden;
    background: var(--stage-grey);
  }
  .business-card {
    position: absolute; left: 75px; top: 200px;
    width: 1050px; height: 600px;
    background: var(--paper-white);
    overflow: hidden;
    box-shadow: 0 6px 24px rgba(0,0,0,0.18);
  }
  .header-band {
    position: absolute; left: 0; top: 0;
    width: 100%; height: 285px;
    background: var(--ink-black);
  }
  .channel-logo {
    position: absolute; left: 40px; top: 28px;
    width: 230px; height: 230px;
    display: flex; flex-direction: column; align-items: center; justify-content: center;
    gap: 16px;
  }
  .channel-logo .logo-dot {
    width: 96px; height: 96px; border-radius: 50%;
    background: var(--brand-orange);
  }
  .channel-logo .logo-name {
    font-family: "Josefin Sans", sans-serif; font-weight: 700;
    font-size: 21px; color: var(--paper-white); text-align: center; line-height: 1.15;
  }
  .channel-title {
    position: absolute; left: 318px; top: 50px;
    font-family: "Josefin Sans", sans-serif; font-weight: 700;
    text-transform: uppercase; line-height: 0.9;
  }
  .channel-title .title-main {
    display: block; color: var(--brand-orange); font-size: 92px; letter-spacing: -1px;
  }
  .channel-title .title-sub {
    display: block; color: var(--paper-white); font-size: 48px; letter-spacing: 3px;
    margin-top: 6px; padding-left: 100px;
  }
  .food-photos {
    position: absolute; right: 0; top: 0;
    width: 345px; height: 100%;
    background: linear-gradient(180deg, #e9e37a 0%, #d9d46a 30%, #5a3a2a 45%, #e85a7a 62%, #3a8fd8 78%, #4cb050 90%, #f0c23a 100%);
  }
  .presenter-name {
    position: absolute; left: 42px; top: 318px;
    font-family: "Josefin Sans", sans-serif; font-weight: 700;
    font-size: 62px; color: var(--brand-orange); text-transform: uppercase;
  }
  .contact-list {
    position: absolute; left: 48px; top: 405px;
    list-style: none;
    font-family: "Open Sans", sans-serif; font-size: 25px; color: var(--text-dark);
    line-height: 1.1;
  }
  .contact-list li { display: flex; align-items: center; gap: 22px; margin-bottom: 18px; }
  .contact-list .channel-square {
    width: 52px; height: 38px; border-radius: 6px; background: var(--video-red); flex: none;
  }
  .contact-list svg { flex: none; }
  .tagline-band {
    position: absolute; left: 0; bottom: 0;
    width: 705px; height: 72px;
    background: var(--brand-orange);
    display: flex; align-items: center; padding-left: 40px;
    font-family: "Josefin Sans", sans-serif; font-weight: 600;
    font-size: 26px; letter-spacing: 1.5px; color: var(--text-dark); text-transform: uppercase;
  }
</style>
</head>
<body>
  <main class="business-card">
    <header class="header-band">
      <div class="channel-logo">
        <span class="logo-dot"></span>
        <span class="logo-name">The Tidy Skillet Show</span>
      </div>
      <h1 class="channel-title">
        <span class="title-main">Tidy</span>
        <span class="title-main">Skillet</span>
        <span class="title-sub">Show</span>
      </h1>
    </header>

    <div class="food-photos" role="img" aria-label="Three food photos: a yellow iced cake with a pool scene on top, a rainbow layer cake filled with candy, and a slice of layered rainbow jelly"></div>

    <h2 class="presenter-name">Marcus Delroy</h2>

    <ul class="contact-list">
      <li>
        <span class="channel-square"></span>
        <span>www.vidloomer.example/user/<br>TidySkilletShow</span>
      </li>
      <li>
        <svg width="52" height="36" viewBox="0 0 52 36" aria-hidden="true">
          <rect x="0" y="0" width="52" height="36" rx="3" fill="var(--mail-blue)"/>
          <polyline points="3,4 26,21 49,4" fill="none" stroke="#ffffff" stroke-width="3"/>
        </svg>
        <span>bookings@harrowlanemedia.example</span>
      </li>
    </ul>

    <footer class="tagline-band">I'll see you next time,&nbsp; for my next meal</footer>
  </main>
</body>
</html>
```